Design für Geburtskarte A6 hoch, Klappkarte
Zielgruppe
Ich bin Fotograf und habe mich auf Schwangerschafts- und Neugeborenenfotografie spezialisiert. Meine Zielgruppe sind schwangere Frauen im letzten Drittel der Schwangerschaft und frisch gewordene Eltern.
Aufgabenstellung
- sehr schlichtes Design, in der Anlage finden Sie zwei der meist verkauften Karten damit Sie sich vom Stil eine Vorstellung machen können
- Lieferung als offene Indesign 5.5 Datei (so das die Farben, Texte, .... angepasst werden können)
- 2-3 Bilder (querformat) sollen in das Design eingearbeitet werden können
- Die Karten werden von mir nachher als fertig gedruckte Karte an meine Kunden verkauft, dies bitte ich zu berücksichtigen
- ich möchte die Karten so nutzen können das sowohl Geburtskarten für Jungs wie auch für Mädels erstellt werden können
- Format: Din A6 (geschlossen 105x148mm), Klappkarte, hoch, 3mm Beschnitt

```html
<!DOCTYPE html>
<html lang="de">
<head>
<meta charset="utf-8">
<title>Geburtskarte Theo – Klappkarte A6</title>
<link href="https://fonts.googleapis.com/css2?family=Kalam:wght@700&family=Dancing+Script:wght@500&family=Crimson+Pro:wght@400&display=swap" rel="stylesheet">
<style>
  :root {
    --page: #ffffff;
    --sheet-line: #cfcfcf;
    --blue-deep: #86a8b9;
    --blue-soft: #adc3ce;
    --fold: #c2d2da;
    --text-light: #ffffff;
    --frame: #ffffff;
    --photo-light: #e9e4df;
    --photo-skin: #d9b8a4;
    --photo-grey: #b9b9bc;
  }
  * { margin: 0; padding: 0; box-sizing: border-box; }
  html, body { width: 848px; height: 1200px; overflow: hidden; background: var(--page); }
  .canvas { position: relative; width: 848px; height: 1200px; }

  .spread {
    position: absolute; left: 51px; width: 763px;
    border: 1px solid var(--sheet-line); background: var(--page);
  }
  .spread--outside { top: 42px; height: 538px; }
  .spread--inside { top: 614px; height: 537px; }
  .spread::after {
    content: ""; position: absolute; top: 0; bottom: 0; left: 381px;
    width: 1px; background: var(--fold);
  }

  .panel { position: absolute; }
  .back-cover { left: 11px; top: 11px; width: 360px; height: 516px; background: var(--blue-deep); }
  .sender {
    position: absolute; left: 21px; bottom: 24px;
    font-family: "Crimson Pro", serif; font-size: 11px; line-height: 14px; color: var(--text-light);
  }

  .front-photo {
    left: 393px; top: 11px; width: 360px; height: 258px;
    background: linear-gradient(135deg, #f4f2f0 0%, var(--photo-light) 45%, var(--photo-skin) 100%);
  }
  .front-info { left: 393px; top: 269px; width: 360px; height: 258px; background: var(--blue-deep); text-align: center; color: var(--text-light); }
  .baby-name {
    margin-top: 56px; font-family: "Kalam", cursive; font-weight: 700; font-size: 58px; line-height: 62px;
    text-shadow: 1px 2px 3px rgba(60, 80, 95, .35);
  }
  .birth-data { font-family: "Dancing Script", cursive; font-size: 22px; line-height: 29px; margin-top: 2px; }

  .inside-bg { left: 11px; top: 10px; width: 741px; height: 516px; background: var(--blue-soft); }
  .headline {
    position: absolute; left: 26px; top: 26px; width: 330px; white-space: nowrap;
    font-family: "Kalam", cursive; font-weight: 700; font-size: 33px; line-height: 40px; color: var(--text-light);
  }
  .message {
    position: absolute; left: 31px; top: 70px; width: 310px;
    font-family: "Crimson Pro", serif; font-size: 11px; line-height: 14px; color: var(--text-light);
  }
  .signature {
    position: absolute; left: 31px; top: 166px;
    font-family: "Crimson Pro", serif; font-size: 11px; line-height: 14px; color: var(--text-light);
  }

  .photo-frame {
    position: absolute; background: var(--frame); padding: 10px;
    box-shadow: 1px 2px 5px rgba(60, 80, 95, .3);
  }
  .photo-frame .photo { width: 100%; height: 100%; }
  .photo-frame--left { left: 21px; top: 213px; width: 322px; height: 226px; }
  .photo-frame--right-top { left: 388px; top: 16px; width: 322px; height: 222px; }
  .photo-frame--right-bottom { left: 390px; top: 252px; width: 326px; height: 226px; transform: rotate(-1.3deg); }
  .photo--sleeping { background: linear-gradient(140deg, #ecebe9 0%, #dcd6d0 50%, var(--photo-skin) 100%); }
  .photo--hand { background: linear-gradient(120deg, #c9a796 0%, #e3cbbd 50%, #9a9ca2 100%); }
  .photo--profile { background: linear-gradient(100deg, #f0efee 0%, var(--photo-grey) 50%, #b88e76 100%); }
</style>
</head>
<body>
<div class="canvas">
  <section class="spread spread--outside">
    <div class="panel back-cover">
      <p class="sender">Anna &amp; Bernd Mustermann<br>Musterstrasse 123<br>99999 Musterstadt</p>
    </div>
    <div class="panel front-photo" role="img" aria-label="Foto: Baby liegt lächelnd auf einer weißen Decke"></div>
    <div class="panel front-info">
      <h1 class="baby-name">Theo</h1>
      <p class="birth-data">14.06.2016 · 14.15 Uhr<br>3000 Gramm · 50 cm</p>
    </div>
  </section>

  <section class="spread spread--inside">
    <div class="panel inside-bg">
      <h2 class="headline">Theo ist endlich da!</h2>
      <p class="message">Lorem ipsum dolor sit amet, consectetuer adipiscing elit. Aenean commodo ligula eget dolor. Aenean massa. Cum sociis natoque penatibus et magnis dis parturient montes, nascetur ridiculus mus. Donec quam felis, ultricies nec, pellentesque eu,</p>
      <p class="signature">Anna &amp; Bernd Mustermann</p>

      <figure class="photo-frame photo-frame--left">
        <div class="photo photo--sleeping" role="img" aria-label="Foto: schlafendes Neugeborenes auf flauschiger Decke"></div>
      </figure>
      <figure class="photo-frame photo-frame--right-top">
        <div class="photo photo--hand" role="img" aria-label="Foto: Babyhand umgreift den Finger eines Elternteils"></div>
      </figure>
      <figure class="photo-frame photo-frame--right-bottom">
        <div class="photo photo--profile" role="img" aria-label="Foto: Neugeborenes im Profil, von einer Hand gehalten"></div>
      </figure>
    </div>
  </section>
</div>
</body>
</html>
```